Brand and Marketing Coach Needs PDF Designed

I have content that i need placed into a simple but great PDF design. The PDF is about the formula I use to build personal brands. This is geared towards entrepreneurs, experts, coaches, therapists, wellness practitioners, and indpendent business owners who serve to improve the lives of others.
The company name is changing from TorvelCast to Selling with the Village (I don't have that logo yet, so working backwards a bit. For now, the TorvelCast logo can be used.) My brand is NOT formal and corporate, but it's also not neon-pink and screaming at you. It's down to earth, hip, a bit modern but warm. It's about no BS and authenticity. The final deliverable should make the reader feel focused, smart, motivated and hopeful.

Target Market(s)

Conscious entrepreneurs and small business owners. this one is specifically for pharmacy entrepreneurs but this will be used for various audiences later.

Font styles to use
Sans Serif

Colors
eaf1f7
3377b5
6b449b
f37122
faa54b
f68e4e
ffc214

Requirements
Must have
• Modern design. colors that match logo - 4e5583 (i think that is the blue.) d65a40.
• Could have these colors as well: c6a254, 01bcc3
• But open to other colors
Nice to have
• I'd like to see some ways to make this PDF simple and readable, and eye-catching. I'd also like to use the uploaded ebooks for design ideas.
Should not have
• neon colors, clip art

```html
<!DOCTYPE html>
<html lang="en">
<head>
<meta charset="utf-8">
<title>Start Here – TorvelCast</title>
<link rel="stylesheet" href="https://fonts.googleapis.com/css2?family=Rajdhani:wght@400;500;600&family=Raleway:wght@100;400&display=swap">
<style>
  :root {
    --page-bg: #ffffff;
    --ink: #3a3a3a;
    --muted: #8a8a8a;
    --purple: #6b449b;
    --brand-blue: #4e5583;
    --numeral: #dcdcdc;
  }
  html, body {
    margin: 0;
    padding: 0;
    overflow: hidden;
    background: var(--page-bg);
  }
  .page {
    position: relative;
    width: 1200px;
    height: 927px;
    overflow: hidden;
    background: var(--page-bg);
    font-family: "Rajdhani", sans-serif;
    color: var(--ink);
  }
  .chapter-number {
    position: absolute;
    left: 204px;
    top: 168px;
    font-family: "Raleway", sans-serif;
    font-weight: 100;
    font-size: 124px;
    line-height: 1;
    color: var(--numeral);
    margin: 0;
  }
  .section-tab {
    position: absolute;
    left: 283px;
    top: 223px;
    width: 233px;
    height: 34px;
  }
  .section-tab svg {
    position: absolute;
    inset: 0;
  }
  .section-title {
    position: relative;
    margin: 0;
    padding-left: 12px;
    font-weight: 500;
    font-size: 32px;
    line-height: 36px;
    color: #ffffff;
    letter-spacing: 0.3px;
  }
  .body-copy {
    position: absolute;
    left: 297px;
    top: 276px;
    width: 767px;
  }
  .body-copy p {
    margin: 0 0 21px;
    font-size: 17.2px;
    font-weight: 500;
    line-height: 19px;
    text-align: justify;
  }
  .footer-rule {
    position: absolute;
    left: 297px;
    top: 846px;
    width: 903px;
    height: 3px;
    background: var(--purple);
  }
  .brand {
    position: absolute;
    left: 55px;
    top: 818px;
    width: 220px;
  }
  .brand-name {
    font-family: "Rajdhani", sans-serif;
    font-weight: 600;
    font-size: 44px;
    line-height: 50px;
    color: var(--brand-blue);
  }
  .brand-tagline {
    margin-top: 2px;
    font-family: "Rajdhani", sans-serif;
    font-weight: 500;
    font-size: 13px;
    letter-spacing: 0.6px;
    color: var(--muted);
    white-space: nowrap;
  }
</style>
</head>
<body>
<main class="page">
  <p class="chapter-number">1</p>

  <div class="section-tab">
    <svg width="233" height="34" viewBox="0 0 233 34" aria-hidden="true">
      <polygon points="0,0 233,0 214,34 0,34" fill="var(--purple)"/>
    </svg>
    <h1 class="section-title">START HERE</h1>
  </div>

  <section class="body-copy">
    <p>Freedom, impact, and profit... one or all of these are the reasons you started, or want to start, a business...</p>
    <p>But right now, you’re wondering how you’re going to stand out from all the online noise.</p>
    <p>Chatterly is supersaturated with experts and businesses offering very similar if not exactly the same things you do, which makes you doubt how doable and realistic this business thing really is.</p>
    <p>Naturally, when faced with this, you rush to create a logo, a website, and a presence on social media. And this is when I start to worry.</p>
    <p>Because that is COMPLETELY BACKWARDS!</p>
    <p>It’s similar to a doctor prescribing medications to treat a patient’s symptoms without identifying and understanding what is causing them. The symptoms could be side effects of another medicine, the results of illness, or could stem from any number of issues.</p>
    <p>Writing your website copy without knowing how to stand apart from others in your industry, position yourself as the expert, or the exact words and phrases that will get your ideal client’s attention is a big waste of your time and money.</p>
    <p>When I see business owners do this, their eBook doesn’t perform as they expected, their website is dead in the water, and they can’t seem to get the right clients.</p>
    <p>What I do for my clients, before I can even begin thinking about their marketing, is to DEFINE them... figure out who they are, what they’re about, and how to differentiate them so they’ll stand out from all the online noise.</p>
    <p>This is the way to build a strong and authentic brand.</p>
  </section>

  <div class="footer-rule"></div>

  <div class="brand">
    <div class="brand-name">TorvelCast</div>
    <div class="brand-tagline">marketing • branding • content</div>
  </div>
</main>
</body>
</html>
```